Business Card Design - Amberfield Court

We are looking at a new design for our business cards that has a modern and professional look. We run a residential aged care facility focussing on the care of residents. The cards will be used for potential clients, consultants and business opportunities in this sector. Blue and white is our main colours and would to see these colours incorporated in the design.
Industry/Entity Type
Business
Contact Information for Business Card
Amberfield Court, Darren Walsh, dwalsh@amberfieldcourt.com.au, Finance Manager, 0472 639 208, BCom, 37 Marrabel Crescent, Brindle Vale, Qld 4093.
Look and feel
Each slider illustrates characteristics of the customer's brand and the style your logo design should communicate.

```html
<!DOCTYPE html>
<html lang="en">
<head>
<meta charset="UTF-8">
<title>Amberfield Court – Business Card</title>
<link href="https://fonts.googleapis.com/css2?family=Arimo:wght@400;700&display=swap" rel="stylesheet">
<style>
  :root {
    --canvas: #e9ebed;
    --paper: #ffffff;
    --blue-light: #5a87a3;
    --blue: #4a7793;
    --blue-deep: #3a6580;
    --ink-on-blue: #ffffff;
    --ink-soft: #e3edf3;
    --shadow: rgba(30, 45, 60, 0.22);
  }
  * { box-sizing: border-box; margin: 0; padding: 0; }
  html, body {
    width: 1200px;
    height: 950px;
    overflow: hidden;
    background: var(--canvas);
    font-family: "Arimo", Arial, sans-serif;
  }
  .sheet {
    width: 1200px;
    height: 950px;
    display: flex;
    flex-direction: column;
    align-items: center;
    justify-content: center;
    gap: 48px;
  }
  .card {
    width: 720px;
    height: 411px;
    box-shadow: 0 10px 28px var(--shadow);
    position: relative;
    overflow: hidden;
  }

  /* Front */
  .card--front { display: flex; background: var(--paper); }
  .front__brand {
    width: 44%;
    flex: none;
    display: flex;
    align-items: center;
    justify-content: center;
    gap: 12px;
    padding: 0 22px;
    min-width: 0;
  }
  .front__details {
    flex: 1;
    min-width: 0;
    background: linear-gradient(100deg, var(--blue-light) 0%, var(--blue) 45%, var(--blue-deep) 100%);
    color: var(--ink-on-blue);
    padding: 92px 24px 0 40px;
  }
  .brand-dot {
    width: 22px;
    height: 22px;
    border-radius: 50%;
    background: var(--blue);
    flex: none;
  }
  .brand-name {
    font-size: 19px;
    font-weight: 400;
    letter-spacing: 1px;
    color: var(--blue);
    text-transform: uppercase;
    white-space: nowrap;
  }
  .person__name {
    font-size: 21px;
    font-weight: 700;
    letter-spacing: 0.5px;
  }
  .person__name .credential { font-size: 17px; }
  .person__role {
    font-size: 17px;
    letter-spacing: 0.5px;
    margin-top: 3px;
    color: var(--ink-soft);
  }
  .address {
    font-style: normal;
    font-size: 16px;
    line-height: 1.35;
    margin-top: 22px;
    color: var(--ink-soft);
  }
  .contact-list { list-style: none; margin-top: 14px; }
  .contact-list li {
    display: flex;
    align-items: center;
    gap: 10px;
    font-size: 16px;
    line-height: 1.65;
    color: var(--ink-soft);
    white-space: nowrap;
  }
  .contact-list svg { width: 16px; height: 16px; flex: none; }

  /* Back */
  .card--back {
    background: linear-gradient(100deg, var(--blue-light) 0%, var(--blue) 50%, var(--blue-deep) 100%);
    display: flex;
    align-items: center;
    justify-content: center;
    gap: 16px;
  }
  .card--back .brand-dot { background: var(--ink-on-blue); width: 26px; height: 26px; }
  .card--back .brand-name { color: var(--ink-on-blue); font-size: 30px; letter-spacing: 1.5px; }
</style>
</head>
<body>
<main class="sheet">
  <section class="card card--front" aria-label="Business card front">
    <div class="front__brand">
      <span class="brand-dot"></span>
      <span class="brand-name">Amberfield Court</span>
    </div>
    <div class="front__details">
      <p class="person__name">DARREN WALSH <span class="credential">BCOM</span></p>
      <p class="person__role">FINANCE MANAGER</p>
      <address class="address">37 Marrabel Crescent<br>Brindle Vale, Qld 4093.</address>
      <ul class="contact-list">
        <li>
          <svg viewBox="0 0 16 16" aria-hidden="true"><path fill="#fff" d="M3 2h3l1.3 3.2-1.8 1.1a8 8 0 0 0 4.2 4.2l1.1-1.8L14 10v3a1 1 0 0 1-1 1A11 11 0 0 1 2 3a1 1 0 0 1 1-1z"/></svg>
          0472 639 208
        </li>
        <li>
          <svg viewBox="0 0 16 16" aria-hidden="true"><rect x="1.5" y="3.5" width="13" height="9" rx="1" fill="#fff"/><path d="M2 4l6 5 6-5" fill="none" stroke="#3a6580" stroke-width="1.3"/></svg>
          dwalsh@amberfieldcourt.com.au
        </li>
        <li>
          <svg viewBox="0 0 16 16" aria-hidden="true"><circle cx="8" cy="8" r="6.5" fill="#fff"/><path d="M1.5 8h13M8 1.5c-2.5 3-2.5 10 0 13M8 1.5c2.5 3 2.5 10 0 13" fill="none" stroke="#3a6580" stroke-width="1"/></svg>
          www.amberfieldcourt.com.au
        </li>
      </ul>
    </div>
  </section>

  <section class="card card--back" aria-label="Business card back">
    <span class="brand-dot"></span>
    <span class="brand-name">Amberfield Court</span>
  </section>
</main>
</body>
</html>
```